Ward Compass Business Card Design*

We need a business card design for our company Ward Compass. Our company is specialized in providing online consulting services regarding medical institutions, hospitals and doctors. We work with patients worldwide looking to choose between healthcare providers. We have a website you may use as a reference, where we list doctors and clinics worldwide. So we target Medical providers as well as patients worldwide.
Target Market(s)
Medical Providers and patients around the world
Industry/Entity Type
Medical
Contact Information for Business Card
Salwa Kettani
CEO
+90 612 348 2175
info@wardcompass.example
www.wardcompass.example
14 Annakhil 7 H.R.B. Rabat, Morocco
Requirements
Must have
- Company logo/name on one full side, personal info and smaller logo and company name on the other side.
Nice to have
- Smart and elegant design

```html
<!DOCTYPE html>
<html lang="en">
<head>
<meta charset="utf-8">
<title>Ward Compass Business Card</title>
<link rel="stylesheet" href="https://fonts.googleapis.com/css2?family=Mulish:wght@300;400;700&display=swap">
<style>
  :root {
    --navy: #1a4373;
    --grey: #7d7b7c;
    --paper: #f3f3f5;
    --white: #ffffff;
    --backdrop: #d8d3cb;
  }
  * { margin: 0; padding: 0; box-sizing: border-box; }
  html, body {
    width: 900px;
    height: 1200px;
    overflow: hidden;
    background: var(--backdrop);
    font-family: "Mulish", "Helvetica Neue", Arial, sans-serif;
  }
  .canvas { position: relative; width: 900px; height: 1200px; }
  .card {
    position: absolute;
    left: 77px;
    width: 746px;
    height: 436px;
    box-shadow: 0 2px 6px rgba(0,0,0,0.25);
  }
  .card--front { top: 134px; background: var(--navy); color: var(--white); }
  .card--back { top: 638px; background: var(--paper); }

  /* Front: brand block */
  .front-brand {
    position: absolute;
    left: 112px;
    top: 192px;
    display: flex;
    align-items: center;
    gap: 14px;
  }
  .front-brand__dot {
    width: 34px; height: 34px;
    border-radius: 50%;
    background: var(--white);
  }
  .front-brand__name {
    font-size: 26px;
    font-weight: 400;
    letter-spacing: 0.5px;
    color: var(--white);
  }

  /* Front: personal details */
  .person {
    position: absolute;
    left: 414px;
    top: 172px;
  }
  .person__name {
    font-size: 24px;
    line-height: 1;
    letter-spacing: 0.3px;
  }
  .person__name strong { font-weight: 700; }
  .person__name span { font-weight: 400; }
  .person__role {
    margin-top: 6px;
    font-size: 18px;
    font-weight: 400;
  }
  .contact {
    list-style: none;
    margin-top: 32px;
  }
  .contact__item {
    display: flex;
    align-items: center;
    gap: 11px;
    font-size: 17px;
    font-weight: 400;
    height: 26px;
    letter-spacing: 0.3px;
  }
  .contact__icon { width: 18px; height: 18px; flex: none; }

  /* Back: brand block */
  .back-brand {
    position: absolute;
    left: 0; right: 0;
    top: 162px;
    display: flex;
    justify-content: center;
    align-items: center;
    gap: 22px;
  }
  .back-brand__dot {
    width: 100px; height: 100px;
    border-radius: 50%;
    background: var(--navy);
  }
  .back-brand__name {
    font-size: 48px;
    font-weight: 400;
    letter-spacing: 1px;
    color: var(--navy);
  }
  .website {
    position: absolute;
    left: 0; right: 0;
    top: 396px;
    text-align: center;
    font-size: 16px;
    font-weight: 400;
    color: #3d3d3d;
    letter-spacing: 0.3px;
  }
</style>
</head>
<body>
<main class="canvas">
  <section class="card card--front" aria-label="Card front">
    <div class="front-brand">
      <div class="front-brand__dot"></div>
      <div class="front-brand__name">Ward Compass</div>
    </div>
    <div class="person">
      <h1 class="person__name"><strong>SALWA</strong> <span>KETTANI</span></h1>
      <p class="person__role">CEO</p>
      <ul class="contact">
        <li class="contact__item">
          <svg class="contact__icon" viewBox="0 0 18 18" aria-hidden="true">
            <circle cx="9" cy="9" r="9" fill="#ffffff"/>
            <path d="M6.2 4.6c.4-.3.9-.2 1.1.2l.8 1.5c.2.4.1.8-.2 1.1l-.5.4c.4 1 1.2 1.8 2.2 2.3l.4-.5c.3-.3.8-.4 1.1-.2l1.5.8c.4.2.5.8.2 1.1l-.6.8c-.4.5-1.1.7-1.7.5-2.5-.8-4.4-2.7-5.2-5.2-.2-.6 0-1.3.5-1.7z" fill="#1a4373"/>
          </svg>
          <span>+90 612 348 2175</span>
        </li>
        <li class="contact__item">
          <svg class="contact__icon" viewBox="0 0 18 18" aria-hidden="true">
            <circle cx="9" cy="9" r="9" fill="#ffffff"/>
            <rect x="4.5" y="5.8" width="9" height="6.4" rx="0.8" fill="#1a4373"/>
            <path d="M4.8 6.3 9 9.4l4.2-3.1" fill="none" stroke="#ffffff" stroke-width="0.9"/>
          </svg>
          <span>info@wardcompass.example</span>
        </li>
      </ul>
    </div>
  </section>

  <section class="card card--back" aria-label="Card back">
    <div class="back-brand">
      <div class="back-brand__dot"></div>
      <div class="back-brand__name">WARD COMPASS</div>
    </div>
    <p class="website">www.wardcompass.example</p>
  </section>
</main>
</body>
</html>
```